business card Calvanto

Wee need a business card design for a new compagny based on Paris
We developped innovative a platform for selling services to refresh, beautify and develop its housing.
We would like a red logo on a black background
Te final design should communicate quality service, know-how, high-end

Target Market(s)

individuals

Industry/Entity Type

Business

```html
<!DOCTYPE html>
<html lang="en">
<head>
<meta charset="utf-8">
<title>Calvanto — Business Card</title>
<link rel="stylesheet" href="https://fonts.googleapis.com/css2?family=Questrial&family=Montserrat:wght@400;700&display=swap">
<style>
  :root {
    --coral: #e4635f;
    --white: #ffffff;
    --grey: #7c7c7c;
    --grey-light: #a9a9a9;
    --ink: #2d2d2d;
    --backdrop: #d9d9d9;
  }
  * { margin: 0; padding: 0; box-sizing: border-box; }
  html, body {
    width: 1200px; height: 852px; overflow: hidden;
    background: var(--backdrop);
  }
  .stage {
    position: relative; width: 1200px; height: 852px;
    display: flex; align-items: center; justify-content: center; gap: 40px;
  }
  .card {
    position: relative; width: 540px; height: 310px;
    border-radius: 24px; overflow: hidden;
    box-shadow: 0 6px 18px rgba(0,0,0,0.18);
  }

  /* Front */
  .card--front { background: var(--coral); }
  .card--front .brand {
    position: absolute; left: 50%; top: 50%;
    transform: translate(-50%, -50%);
    display: flex; align-items: center; gap: 14px;
  }
  .card--front .brand__mark { width: 58px; height: 58px; background: var(--white); }
  .card--front .brand__name {
    font-family: "Questrial", sans-serif;
    font-size: 56px; color: var(--white); line-height: 1;
  }

  /* Back */
  .card--back { background: var(--white); }
  .card--back .waves { position: absolute; inset: 0; }
  .card--back .brand {
    position: absolute; left: 36px; top: 132px;
    display: flex; align-items: center; gap: 12px;
  }
  .card--back .brand__mark { width: 50px; height: 50px; background: var(--coral); }
  .card--back .brand__name {
    font-family: "Questrial", sans-serif;
    font-size: 44px; color: var(--grey); line-height: 1;
  }
  .person { position: absolute; left: 38px; top: 204px; }
  .person__name {
    font-family: "Montserrat", sans-serif; font-weight: 700;
    font-size: 15px; color: var(--coral);
  }
  .person__role {
    font-family: "Montserrat", sans-serif; font-weight: 400;
    font-size: 10.5px; color: var(--ink); margin-top: 3px;
  }
  .contact {
    position: absolute; right: 24px; top: 92px;
    list-style: none; text-align: right;
    font-family: "Montserrat", sans-serif; font-size: 9.5px;
    color: var(--white); line-height: 19px;
  }
  .contact li { display: flex; justify-content: flex-end; align-items: center; gap: 6px; }
  .contact svg { width: 10px; height: 10px; flex: none; }
</style>
</head>
<body>
<main class="stage">
  <section class="card card--front" aria-label="Card front">
    <div class="brand">
      <span class="brand__mark"></span>
      <span class="brand__name">Calvanto</span>
    </div>
  </section>

  <section class="card card--back" aria-label="Card back">
    <svg class="waves" viewBox="0 0 540 310" preserveAspectRatio="none" aria-hidden="true">
      <path fill="var(--coral)" d="M540,30 C470,45 400,70 360,110 C325,150 315,190 290,235 C240,290 120,292 0,295 L0,310 L540,310 Z"/>
      <path fill="none" stroke="var(--grey)" stroke-width="7" transform="translate(-10,-9)" d="M540,30 C470,45 400,70 360,110 C325,150 315,190 290,235 C240,290 120,292 0,295"/>
      <path fill="none" stroke="var(--grey-light)" stroke-width="3" transform="translate(-20,-19)" d="M540,30 C470,45 400,70 360,110 C325,150 315,190 290,235 C240,290 120,292 0,295"/>
    </svg>

    <div class="brand">
      <span class="brand__mark"></span>
      <span class="brand__name">Calvanto</span>
    </div>

    <div class="person">
      <p class="person__name">Your Long Name</p>
      <p class="person__role">Managing Director</p>
    </div>

    <ul class="contact">
      <li>00.00.00.0000
        <svg viewBox="0 0 10 10"><path fill="#fff" d="M2 1 L4 1 L4.5 3 L3.3 4 Q4 6 6 6.7 L7 5.5 L9 6 L9 8 Q9 9 8 9 Q1 8.5 1 2 Q1 1 2 1Z"/></svg>
      </li>
      <li>00.00.00.0000
        <svg viewBox="0 0 10 10"><rect x="1" y="3" width="8" height="6" fill="none" stroke="#fff"/><rect x="3" y="1" width="4" height="3" fill="#fff"/></svg>
      </li>
      <li>www.yourwebsite.com
        <svg viewBox="0 0 10 10"><circle cx="5" cy="5" r="4" fill="none" stroke="#fff"/><path d="M1 5 H9 M5 1 V9" stroke="#fff" stroke-width=".8"/></svg>
      </li>
      <li>yourname@yourwebsite.com
        <svg viewBox="0 0 10 10"><rect x="1" y="2" width="8" height="6" fill="none" stroke="#fff"/><path d="M1 2 L5 5.5 L9 2" fill="none" stroke="#fff"/></svg>
      </li>
      <li>Your Commercial or office address
        <svg viewBox="0 0 10 10"><path fill="#fff" d="M5 10 L2 5.5 A3.5 3.5 0 1 1 8 5.5 Z"/><circle cx="5" cy="3.6" r="1.2" fill="var(--coral)"/></svg>
      </li>
    </ul>
  </section>
</main>
</body>
</html>
```